New Business Card Design Project

I'd like a business card design around the same modern style that I used on my website www.brovanhs.com
It's gonna be one of those round corners double-sided business cards with maybe a big logo on the front and all the info on the back of the card.

Contact Information for Business Card

Marco Delgado
425-317-6084
www.brovanhs.com

www.facebook.com/BrovanHomeServices
www.intsgram.com/BrovanHomeServices

Requirements
Must have
• it needs to look elegant and modern

```html
<!DOCTYPE html>
<html lang="en">
<head>
<meta charset="utf-8">
<title>Brovan Home Services – Business Card</title>
<link href="https://fonts.googleapis.com/css2?family=Montserrat:wght@500;700;800&display=swap" rel="stylesheet">
<style>
  :root{
    --stage:#16171a;
    --card:#222528;
    --card-edge:#2a2e31;
    --blue:#1d9be6;
    --blue-deep:#1477c4;
    --white:#f4f6f8;
    --muted:#c9ced3;
    --decor:#2c3a40;
  }
  *{box-sizing:border-box;margin:0;padding:0}
  html,body{width:1200px;height:800px;overflow:hidden;background:var(--stage);font-family:"Montserrat",sans-serif}
  .stage{position:relative;width:1200px;height:800px;display:flex;align-items:center;justify-content:center;gap:40px}
  .card{position:relative;width:540px;height:309px;background:var(--card);border-radius:16px;border:1px solid var(--card-edge);overflow:hidden;box-shadow:0 18px 40px rgba(0,0,0,.45)}

  /* front */
  .card-front{display:flex;align-items:center;justify-content:center;gap:16px}
  .brand-dot{width:26px;height:26px;border-radius:50%;background:var(--blue);flex:none}
  .brand-name{color:var(--blue);font-weight:800;font-size:38px;line-height:1.05;letter-spacing:.5px}

  /* back */
  .decor-field{position:absolute;right:0;top:0;width:300px;height:190px;
    background:radial-gradient(ellipse at 70% 35%, var(--decor) 0%, rgba(44,58,64,.35) 45%, rgba(34,37,40,0) 75%)}
  .back-brand{position:absolute;left:34px;top:78px;display:flex;align-items:center;gap:10px}
  .back-brand .brand-dot{width:16px;height:16px}
  .back-brand .brand-name{font-size:24px}
  .rule{position:absolute;left:30px;right:30px;top:212px;height:2px;background:var(--blue)}
  .person-name{position:absolute;left:34px;top:180px;color:var(--white);font-weight:700;font-size:19px}
  .contact-list{position:absolute;left:34px;top:226px;list-style:none;display:flex;flex-direction:column;gap:8px}
  .social-list{position:absolute;right:30px;top:150px;list-style:none;display:flex;flex-direction:column;gap:6px}
  .contact-item{display:flex;align-items:center;gap:8px;color:var(--white);font-size:13px;font-weight:500}
  .icon{width:16px;height:16px;border-radius:3px;background:var(--blue);display:flex;align-items:center;justify-content:center;flex:none}
  .icon svg{width:11px;height:11px}
  .social-square{width:14px;height:14px;border-radius:2px;background:var(--blue);flex:none}
  .accent{color:var(--blue)}
</style>
</head>
<body>
<main class="stage">
  <section class="card card-front" aria-label="Card front">
    <span class="brand-dot"></span>
    <h1 class="brand-name">Brovan<br>Home Services</h1>
  </section>

  <section class="card card-back" aria-label="Card back">
    <div class="decor-field" role="img" aria-label="Faint sparkle pattern decoration"></div>
    <div class="back-brand">
      <span class="brand-dot"></span>
      <span class="brand-name">Brovan Home Services</span>
    </div>

    <p class="person-name">Marco Delgado</p>
    <ul class="social-list">
      <li class="contact-item"><span class="social-square"></span>BrovanHomeServices</li>
      <li class="contact-item"><span class="social-square"></span>BrovanHomeServices</li>
    </ul>
    <div class="rule"></div>

    <ul class="contact-list">
      <li class="contact-item">
        <span class="icon"><svg viewBox="0 0 24 24"><path fill="#fff" d="M6.6 10.8a15.1 15.1 0 0 0 6.6 6.6l2.2-2.2c.3-.3.7-.4 1-.2 1.1.4 2.3.6 3.6.6.6 0 1 .4 1 1V20c0 .6-.4 1-1 1A17 17 0 0 1 3 4c0-.6.4-1 1-1h3.5c.6 0 1 .4 1 1 0 1.3.2 2.5.6 3.6.1.3 0 .7-.2 1z"/></svg></span>
        425-317-6084
      </li>
      <li class="contact-item">
        <span class="icon"><svg viewBox="0 0 24 24" fill="none" stroke="#fff" stroke-width="2"><circle cx="12" cy="12" r="9"/><path d="M3 12h18M12 3c3 3 3 15 0 18M12 3c-3 3-3 15 0 18"/></svg></span>
        <span>www.<span class="accent">brovanhs</span>.com</span>
      </li>
    </ul>
  </section>
</main>
</body>
</html>
```